Business Card Design for Software Development Company

I am looking for a business card design the incorporates my new logo (attached below).

Key information to include:
Name: Martin Quelbrook
Title: CEO
Email: martin@brightwellcivic.example
Phone: 555-218-9403
Website: www.brightwellcivic.example

NOTE: This design should be easy to edit so that we can order cards for different members of our team.

```html
<!DOCTYPE html>
<html lang="en">
<head>
<meta charset="utf-8">
<title>Brightwell Labs Business Card</title>
<link href="https://fonts.googleapis.com/css2?family=Montserrat:wght@400;500;600;700&display=swap" rel="stylesheet">
<style>
  :root {
    --page-bg: #e4e2e3;
    --card-white: #ffffff;
    --card-slate: #6f789c;
    --ink: #1d1d24;
    --brand-navy: #3a3f57;
    --brand-deep: #474d6b;
    --accent-orange: #e8793a;
  }
  * { margin: 0; padding: 0; box-sizing: border-box; }
  html, body {
    width: 1200px;
    height: 1108px;
    overflow: hidden;
    background: var(--page-bg);
    font-family: "Montserrat", Arial, sans-serif;
    color: var(--ink);
  }
  .card {
    position: absolute;
    left: 228px;
    width: 756px;
  }
  .card-front {
    top: 56px;
    height: 462px;
    background: var(--card-white);
  }
  .card-back {
    top: 575px;
    height: 444px;
    background: var(--card-slate);
  }
  .brand {
    position: absolute;
    display: flex;
    align-items: center;
    gap: 10px;
    font-weight: 700;
    white-space: nowrap;
  }
  .brand-mark { flex: none; }
  .card-front .brand {
    left: 96px;
    top: 242px;
    font-size: 30px;
    color: var(--brand-navy);
    letter-spacing: -0.5px;
  }
  .card-front .brand-mark { width: 18px; height: 18px; background: var(--accent-orange); }
  .card-back .brand {
    left: 0;
    right: 0;
    top: 196px;
    justify-content: center;
    font-size: 56px;
    color: var(--brand-deep);
    letter-spacing: -1px;
  }
  .card-back .brand-mark { width: 34px; height: 34px; background: var(--accent-orange); }
  .divider {
    position: absolute;
    left: 374px;
    top: 178px;
    width: 1.5px;
    height: 148px;
    background: var(--accent-orange);
  }
  .contact {
    position: absolute;
    left: 388px;
    top: 178px;
  }
  .contact-name {
    font-size: 29px;
    font-weight: 600;
    color: var(--accent-orange);
    line-height: 34px;
  }
  .contact-title {
    font-size: 17px;
    line-height: 24px;
    margin-bottom: 4px;
  }
  .contact-list { list-style: none; }
  .contact-list li {
    display: flex;
    align-items: center;
    gap: 9px;
    font-size: 17.5px;
    line-height: 29px;
  }
  .contact-list svg { width: 15px; height: 15px; flex: none; fill: var(--accent-orange); }
  .address {
    position: absolute;
    left: 0;
    right: 0;
    top: 403px;
    text-align: center;
    font-size: 17px;
  }
</style>
</head>
<body>
  <section class="card card-front">
    <div class="brand"><span class="brand-mark"></span>Brightwell Labs</div>
    <div class="divider"></div>
    <div class="contact">
      <p class="contact-name">Martin Quelbrook</p>
      <p class="contact-title">CEO</p>
      <ul class="contact-list">
        <li>
          <svg viewBox="0 0 16 16" aria-hidden="true"><path d="M3.6 1.2l2.3 2.6-1.3 1.8c.9 2 2.6 3.6 4.5 4.6l1.7-1.3 2.7 2.2-1.1 2.4c-5.2-.4-10-5.3-10.3-10.6z"/></svg>
          555-218-9403
        </li>
        <li>
          <svg viewBox="0 0 16 16" aria-hidden="true"><path d="M1 3.5h14v1.2L8 9 1 4.7z"/><path d="M1 6.3l7 4.3 7-4.3v6.2H1z"/></svg>
          martin@brightwellcivic.example
        </li>
        <li>
          <svg viewBox="0 0 16 16" aria-hidden="true"><circle cx="8" cy="8" r="7"/><path d="M4 5.5c1.5 0 2 1 3 1.8s-.5 2.2.8 3-1 2.7-.5 3.5M10 2.8c-.5 1.2.8 2 1.8 2.2s.8 1.8 1.9 2" stroke="#fff" stroke-width="1.2" fill="none"/></svg>
          www.brightwellcivic.example
        </li>
      </ul>
    </div>
    <p class="address">418 Harlow Ave, #112 Fenmoor, OH 43099</p>
  </section>

  <section class="card card-back">
    <div class="brand"><span class="brand-mark"></span>Brightwell Labs</div>
  </section>
</body>
</html>
```